Laser Tattoo Removal Business Cards

We are looking for a professional business card design for a laser tattoo removal business. Ideally looking for a black business card design. The name of the business is Brightline Tattoo Removal. We place our cards at local tattoo shops so we ideally are looking for something trendy/edgy to draw both male and female clientele in.

Target Market(s)

Male/Female ages 18-60

Contact Information for Business Card

black background ideally.. hoping to stay within greys, whites and black

Font styles to use
Serif
Sans Serif

Colors
121212
a9a9a9
5c5c5c
f5f5f5
ffffff
7f7f7f
606060
848484
9d9d9d

Requirements
Must have
• Employee Info:
• Melissa Thornbury
• Chief Executive Offer
• m: 919.537.2846
• w: 919.362.4178
• f: 919.685.3907
• mthornbury@brightlinetattooremoval.example
• Address:
• 4615 Oakmere Pkwy, Suite 210
• Raleigh, NC 27654
• Website:
• www.brightlinetattooremoval.example
Nice to have
• Myabe business name on back or logo on back and employee info on the front

```html
<!DOCTYPE html>
<html lang="en">
<head>
<meta charset="utf-8">
<title>Brightline Tattoo Removal – Business Card</title>
<link rel="stylesheet" href="https://fonts.googleapis.com/css2?family=Roboto:wght@400;500;700&display=swap">
<style>
  :root {
    --ink: #121212;
    --mist: #a9a9a9;
    --slate: #5c5c5c;
    --paper: #f5f5f5;
    --white: #ffffff;
    --grey: #7f7f7f;
    --grey-dark: #606060;
    --grey-mid: #848484;
    --silver: #9d9d9d;
    --backdrop: #e6e6e6;
    --mark: #d6d6d6;
  }
  * { box-sizing: border-box; margin: 0; padding: 0; }
  html, body { width: 1200px; height: 969px; overflow: hidden; }
  body {
    background: var(--backdrop);
    font-family: "Roboto", Arial, sans-serif;
    position: relative;
  }
  .card {
    position: absolute;
    left: 100px; top: 199px;
    width: 1000px; height: 571px;
    background: linear-gradient(135deg, var(--white) 0%, var(--paper) 55%, #ececec 100%);
    border-radius: 6px;
    box-shadow: 0 6px 24px rgba(0,0,0,0.15);
    overflow: hidden;
  }
  .card__details {
    position: absolute;
    left: 58px; top: 112px;
    width: 450px;
    color: #333;
    white-space: nowrap;
  }
  .person__name {
    font-size: 30px; font-weight: 700;
    color: var(--ink);
    letter-spacing: 0.3px;
    text-transform: uppercase;
  }
  .person__title {
    font-size: 22px; color: var(--grey);
    margin-top: 4px;
  }
  .rule {
    width: 42px; height: 2px;
    background: var(--ink);
    margin: 20px 0 18px;
  }
  .address { font-size: 22px; line-height: 30px; color: #2a2a2a; }
  .contacts { list-style: none; }
  .contacts li {
    display: flex; align-items: center;
    font-size: 19.5px; line-height: 31px; color: #2a2a2a;
  }
  .contacts svg { width: 17px; height: 17px; margin-right: 12px; fill: var(--slate); flex: none; }
  .card__brand {
    position: absolute;
    left: 540px; top: 0;
    width: 460px; height: 571px;
    background: var(--ink);
    border-top-left-radius: 72px;
    display: flex; flex-direction: column;
    align-items: center; justify-content: center;
    color: var(--mark);
    font-weight: 500;
    text-transform: uppercase;
  }
  .brand__name { font-size: 62px; letter-spacing: 4px; line-height: 1; }
  .brand__sub { font-size: 24px; letter-spacing: 5px; margin-top: 26px; }
</style>
</head>
<body>
  <article class="card">
    <section class="card__details">
      <h1 class="person__name">Melissa Thornbury</h1>
      <p class="person__title">Chief Executive Offer</p>
      <div class="rule"></div>
      <p class="address">4615 Oakmere Pkwy, Suite 210<br>Raleigh, NC 27654</p>
      <div class="rule"></div>
      <ul class="contacts">
        <li><svg viewBox="0 0 24 24"><path d="M6.6 10.8c1.4 2.8 3.8 5.1 6.6 6.6l2.2-2.2c.3-.3.7-.4 1-.2 1.1.4 2.3.6 3.6.6.6 0 1 .4 1 1V20c0 .6-.4 1-1 1C10.6 21 3 13.4 3 4c0-.6.4-1 1-1h3.5c.6 0 1 .4 1 1 0 1.3.2 2.5.6 3.6.1.3 0 .7-.2 1l-2.3 2.2z"/></svg>919.362.4178</li>
        <li><svg viewBox="0 0 24 24"><path d="M7 1h10a2 2 0 0 1 2 2v18a2 2 0 0 1-2 2H7a2 2 0 0 1-2-2V3a2 2 0 0 1 2-2zm0 3v14h10V4H7zm5 15.2a1.2 1.2 0 1 0 0 2.4 1.2 1.2 0 0 0 0-2.4z"/></svg>919.537.2846</li>
        <li><svg viewBox="0 0 24 24"><path d="M6 2h9l3 3v4h1a3 3 0 0 1 3 3v7h-4v3H6v-3H2v-7a3 3 0 0 1 3-3h1V2zm2 2v5h8V6h-2V4H8zm0 12v4h8v-4H8z"/></svg>919.685.3907</li>
        <li><svg viewBox="0 0 24 24"><path d="M2 5h20v14H2V5zm2 2v.5l8 5 8-5V7H4zm0 2.8V17h16V9.8l-8 5-8-5z"/></svg>mthornbury@brightlinetattooremoval.example</li>
        <li><svg viewBox="0 0 24 24"><circle cx="12" cy="12" r="10"/></svg>www.brightlinetattooremoval.example</li>
      </ul>
    </section>
    <section class="card__brand">
      <p class="brand__name">Brightline</p>
      <p class="brand__sub">Tattoo Removal</p>
    </section>
  </article>
</body>
</html>
```